Northvale Strategy Partners Website Design

I need a website design for my new business consulting and executive coaching firm, Northvale Strategy Partners. We provide consultative services to business C-suites as well as personal coaching to executives. I have attached the logo with color scheme I have chosen. I would like the website to reflect professionalism and continue the color scheme in the logo.

Target Market(s)

Small to medium business and their executives; middle to upper income men and women in mid- to late career looking for significance

Industry/Entity Type

Business Consultant

Number of Pages Required

4 page

Requirements
Must have
• A homepage with prominent logo and way to contact for more information; an area on the homepage with easy to read, clear text to describe what the company does; a prominent area on the homepage for a tagline; a blog page that can be updated regularly, an "about us" page with biographical information; an "about us" page; a page detailing services offered
• The web design must match the logo colors and font that I have uploaded.
Nice to have
• A lighthouse picture in the background or header
Should not have
• A lot of text area on the homepage

```html
<!DOCTYPE html>
<html lang="en">
<head>
<meta charset="utf-8">
<title>Northvale Strategy Partners</title>
<link rel="stylesheet" href="https://fonts.googleapis.com/css2?family=Oswald:wght@400;500&family=Roboto:wght@400;500;700&display=swap">
<style>
:root{
  --navy:#1d2746;
  --red:#c3262c;
  --band-top:#2c467c;
  --band-low:#3f5c96;
  --light:#f1f1f2;
  --card:#ffffff;
  --text:#3a3f4a;
  --muted:#7b808a;
  --footer:#eeeeee;
  --bottom:#1f1f22;
}
*{margin:0;padding:0;box-sizing:border-box}
html,body{width:723px;height:1200px;overflow:hidden}
body{font-family:"Roboto",Arial,sans-serif;color:var(--text);background:#fff}

.site-header{height:68px;display:flex;align-items:center;justify-content:space-between;padding:0 34px 0 28px;background:#fff}
.brand{display:flex;align-items:center;gap:7px}
.brand-mark{width:12px;height:12px;background:var(--navy)}
.brand-name{font-weight:700;font-size:10px;letter-spacing:.6px;color:var(--navy);line-height:1}
.main-nav{display:flex;align-items:center;gap:16px;font-size:8px;font-weight:500;color:var(--navy);text-transform:uppercase}
.main-nav .active{color:var(--red)}
.login-btn{background:var(--navy);color:#fff;padding:6px 12px;border-radius:2px;font-size:8px}

.hero{position:relative;height:347px;
  background:
    radial-gradient(ellipse 120px 170px at 530px 150px,rgba(210,220,235,.55),rgba(210,220,235,0) 100%),
    radial-gradient(ellipse 340px 90px at 560px 260px,rgba(150,170,200,.45),rgba(150,170,200,0) 100%),
    linear-gradient(180deg,#121c33 0%,#22345a 35%,#3e5479 62%,#2a3a58 78%,#141b2c 100%)}
.hero-copy{position:absolute;left:60px;top:150px;color:#fff}
.hero-title{font-family:"Oswald",Arial,sans-serif;font-weight:400;font-size:23px;letter-spacing:.3px}
.hero-tagline{font-family:"Oswald",Arial,sans-serif;font-size:16px;font-weight:400;margin-top:2px;color:#e8ecf4}
.hero-arrows{position:absolute;left:60px;top:243px;display:flex;gap:3px}
.hero-arrows span{width:14px;height:14px;background:rgba(0,0,0,.55);display:flex;align-items:center;justify-content:center}

.services{height:275px;background:var(--light);padding-top:40px}
.section-title{font-family:"Oswald",Arial,sans-serif;font-weight:400;font-size:18px;text-align:center;color:var(--navy);text-transform:uppercase}
.section-title .accent{color:var(--red)}
.section-rule{width:40px;height:2px;background:var(--red);margin:6px auto 0}
.service-list{display:flex;justify-content:center;gap:18px;margin-top:22px}
.service-card{width:150px;height:148px;text-align:center;padding-top:14px}
.service-card.featured{background:var(--card);box-shadow:0 3px 12px rgba(0,0,0,.18)}
.service-icon{width:38px;height:38px;border-radius:50%;background:#fff;border:2px solid var(--navy);margin:0 auto;display:flex;align-items:center;justify-content:center}
.service-card.featured .service-icon{background:var(--navy)}
.service-name{font-size:7px;font-weight:700;color:var(--navy);margin-top:12px;text-transform:uppercase}
.service-text{font-size:6px;color:var(--muted);line-height:1.45;margin:6px 16px 0}
.read-more{display:inline-block;margin-top:8px;font-size:6px;border:1px solid #b9bcc4;padding:3px 7px;color:var(--navy);background:#fff}

.coaching{height:245px;background:linear-gradient(180deg,var(--band-top),var(--band-low));padding-top:22px}
.coaching .section-title{color:#fff}
.coach-list{display:flex;justify-content:center;gap:4px;margin-top:16px}
.coach-card{width:204px;height:156px;position:relative;overflow:hidden}
.coach-card.group{background:linear-gradient(180deg,#eef2f6 0%,#c9d3df 45%,#4a5366 75%,#2a2f3c 100%)}
.coach-card.office{background:linear-gradient(180deg,#b9d3ea 0%,#8fb1d1 40%,#3a4457 70%,#22262f 100%)}
.coach-card.city{background:linear-gradient(180deg,#d7dde4 0%,#a9b3c0 40%,#333945 72%,#1e2129 100%)}
.coach-caption{position:absolute;left:0;right:0;bottom:0;height:22px;background:rgba(20,26,40,.85);color:#fff;font-family:"Oswald",Arial,sans-serif;font-size:8px;letter-spacing:.4px;display:flex;align-items:center;justify-content:center}

.partners{height:75px;display:flex;align-items:center;justify-content:center;gap:46px;background:#fff}
.partner{display:flex;align-items:center;gap:5px;font-size:11px;font-weight:500;color:#4a4d55}
.partner i{width:10px;height:10px;background:#4a4d55;display:block}

.site-footer{height:160px;background:var(--footer);display:flex;gap:26px;padding:20px 30px 0 40px}
.footer-col{width:140px;font-size:6px;color:var(--muted);line-height:1.6}
.footer-col h4{font-size:7px;font-weight:700;color:var(--navy);text-transform:uppercase;margin-bottom:8px}
.footer-col li{list-style:none}
.footer-col li::before{content:"› ";color:var(--red)}
.subscribe{display:flex;margin-top:8px}
.subscribe span{flex:1;background:#fff;border:1px solid #d3d5da;padding:3px 4px;font-size:6px}
.subscribe b{background:var(--red);color:#fff;font-weight:500;padding:3px 6px;font-size:6px}
.social{display:flex;gap:6px;margin-top:12px;justify-content:center}
.social i{width:16px;height:16px;border-radius:50%;border:1px solid #b9bcc4;display:block}

.bottom-bar{height:30px;background:var(--bottom);color:#a8abb3;font-size:6px;display:flex;align-items:center;justify-content:center}
</style>
</head>
<body>
<header class="site-header">
  <div class="brand"><span class="brand-mark"></span><span class="brand-name">NORTHVALE STRATEGY PARTNERS</span></div>
  <nav class="main-nav">
    <span class="active">Home</span><span>About Us</span><span>Services</span><span>Projects</span><span>Coaching</span><span>Blog</span><span>Contacts</span>
    <span class="login-btn">Login</span>
  </nav>
</header>

<section class="hero" role="img" aria-label="Night seascape with a white lighthouse on a rocky shore under a deep blue sky">
  <div class="hero-copy">
    <h1 class="hero-title">NORTHVALE STRATEGY PARTNERS</h1>
    <p class="hero-tagline">Business consulting and executive coaching</p>
  </div>
  <div class="hero-arrows">
    <span><svg width="6" height="8" viewBox="0 0 6 8"><path d="M5 0L1 4l4 4" stroke="#fff" fill="none" stroke-width="1.4"/></svg></span>
    <span><svg width="6" height="8" viewBox="0 0 6 8"><path d="M1 0l4 4-4 4" stroke="#fff" fill="none" stroke-width="1.4"/></svg></span>
  </div>
</section>

<section class="services">
  <h2 class="section-title">Our <span class="accent">Services</span></h2>
  <div class="section-rule"></div>
  <div class="service-list">
    <article class="service-card featured">
      <div class="service-icon"><svg width="18" height="16" viewBox="0 0 18 16"><rect x="1" y="4" width="16" height="11" rx="1.5" fill="none" stroke="#fff" stroke-width="1.6"/><path d="M6 4V2h6v2" fill="none" stroke="#fff" stroke-width="1.6"/><path d="M1 9h16" stroke="#c3262c" stroke-width="1.6"/></svg></div>
      <h3 class="service-name">C-Suites</h3>
      <p class="service-text">Strategy support for leaders shaping the future of growing firms.</p>
      <span class="read-more">Read More</span>
    </article>
    <article class="service-card">
      <div class="service-icon"><svg width="16" height="16" viewBox="0 0 16 16"><circle cx="8" cy="5" r="3.2" fill="#c3262c"/><path d="M2 15c0-3.5 2.7-5.5 6-5.5s6 2 6 5.5z" fill="#1d2746"/></svg></div>
      <h3 class="service-name">Personal Coaching</h3>
      <p class="service-text">One to one guidance for executives seeking clear direction.</p>
      <span class="read-more">Read More</span>
    </article>
    <article class="service-card">
      <div class="service-icon"><svg width="16" height="16" viewBox="0 0 16 16"><rect x="2" y="9" width="3" height="5" fill="#1d2746"/><rect x="6.5" y="6" width="3" height="8" fill="#1d2746"/><rect x="11" y="2" width="3" height="12" fill="#c3262c"/></svg></div>
      <h3 class="service-name">Consultative Services</h3>
      <p class="service-text">Practical plans that turn business goals into daily results.</p>
      <span class="read-more">Read More</span>
    </article>
    <article class="service-card">
      <div class="service-icon"><svg width="16" height="16" viewBox="0 0 16 16"><path d="M2 13L13 3" stroke="#1d2746" stroke-width="2"/><path d="M7 2.5h7v7z" fill="#c3262c"/></svg></div>
      <h3 class="service-name">Advisory Group</h3>
      <p class="service-text">Trusted peer counsel for owners of small and mid firms.</p>
      <span class="read-more">Read More</span>
    </article>
  </div>
</section>

<section class="coaching">
  <h2 class="section-title">Executive Coaching</h2>
  <div class="coach-list">
    <div class="coach-card group" role="img" aria-label="Group of business professionals standing together in an office">
      <div class="coach-caption">NEQUE PORRO QUISQUAM</div>
    </div>
    <div class="coach-card office" role="img" aria-label="Executive in a suit standing in a bright glass office">
      <div class="coach-caption">NEQUE PORRO QUISQUAM</div>
    </div>
    <div class="coach-card city" role="img" aria-label="Smiling businessman with arms crossed in a city office">
      <div class="coach-caption">NEQUE PORRO QUISQUAM</div>
    </div>
  </div>
</section>

<section class="partners">
  <span class="partner"><i></i>Pressline</span>
  <span class="partner"><i></i>Joinwork</span>
  <span class="partner"><i></i>Magenta Cart</span>
  <span class="partner"><i></i>Droplet</span>
  <span class="partner"><i></i>Queryset</span>
</section>

<footer class="site-footer">
  <div class="footer-col">
    <h4>Links</h4>
    <ul>
      <li>Customer Support</li><li>Documentation</li><li>Resources</li><li>Service Plans</li>
    </ul>
  </div>
  <div class="footer-col">
    <h4>Northvale Strategy Partners</h4>
    <p>We help small and mid sized firms and their leaders find focus, build strong teams and grow with purpose.</p>
    <p style="margin-top:6px">Our coaches bring years of practice in business and personal leadership.</p>
  </div>
  <div class="footer-col">
    <h4>Get in Touch</h4>
    <p>Address: 1200 Harbor Lane</p>
    <p>North Bay, NV</p>
    <p>Phone: (555) 014-2200</p>
    <p>Email: info@northvale.com</p>
  </div>
  <div class="footer-col">
    <h4>Newsletter</h4>
    <p>Sign up for news and updates sent to your inbox.</p>
    <div class="subscribe"><span>Enter address</span><b>Subscribe</b></div>
    <div class="social"><i></i><i></i><i></i></div>
  </div>
</footer>
<div class="bottom-bar">Copyright © 2016. All Rights Reserved.</div>
</body>
</html>
```